Bramble Hockey Academy

We are are Ice Hockey Development Company that provided on-ice Hockey development services. We need a Landing Page with tabs to direct to individual program pages.
Landing Page
About Page
Winter Program Page
Spring Program Page
Summer Program Page
Team Page
Tournament Page

Coded - Design and coding required

5+ page

```html
<!DOCTYPE html>
<html lang="en">
<head>
<meta charset="utf-8">
<title>Bramble Hockey Academy</title>
<link rel="stylesheet" href="https://fonts.googleapis.com/css2?family=Audiowide&family=Nunito+Sans:wght@400;600;700;800&display=swap">
<style>
:root{
  --green:#1f8a1f;
  --green-dark:#176d17;
  --green-deep:#0f4f10;
  --green-bright:#27a52a;
  --ink:#1d1d1d;
  --text:#3d3d3d;
  --muted:#6a6a6a;
  --line:#e4e4e4;
  --white:#ffffff;
  --footer:#2b2b2b;
}
*{box-sizing:border-box;margin:0;padding:0}
html,body{width:1200px;height:3298px;overflow:hidden}
body{position:relative;background:var(--white);font-family:"Nunito Sans",sans-serif;color:var(--text)}
.abs{position:absolute}
a{color:inherit;text-decoration:none}

/* header */
.site-header{left:0;top:0;width:1200px;height:88px;background:var(--white)}
.brand{left:111px;top:24px;font-weight:800;font-size:22px;line-height:22px;color:var(--ink);width:160px;text-transform:uppercase;letter-spacing:.5px}
.main-nav{left:499px;top:32px;display:flex;gap:30px;font-size:17px;color:var(--ink)}
.main-nav .active{color:var(--green)}
.social{left:955px;top:31px;display:flex;gap:10px}
.social span{width:26px;height:26px;border-radius:50%;background:var(--green-dark);display:block}

/* hero */
.hero{left:0;top:88px;width:1200px;height:470px;overflow:hidden}
.hero-photo{left:0;top:0;width:1200px;height:470px;background:linear-gradient(120deg,#d9dde0 0%,#a9b0b5 35%,#7d858a 60%,#c7ccd0 100%)}
.hero-green{left:0;top:0;width:1200px;height:470px;background:linear-gradient(135deg,#1e9a1e,#137213 60%,#0d5a0d);clip-path:polygon(685px 0,1200px 0,1200px 470px,548px 470px)}
.hero-copy{left:620px;top:128px;width:500px;text-align:center;color:var(--white)}
.hero-welcome{font-size:31px;font-weight:600;display:inline-block;padding-bottom:8px;border-bottom:2px solid var(--white)}
.hero-title{font-family:"Audiowide",sans-serif;font-size:45px;line-height:58px;margin-top:20px}
.btn-outline{display:inline-block;border:2px solid var(--white);border-radius:6px;color:var(--white);font-weight:600;font-size:16px;padding:12px 25px}
.hero .btn-outline{margin-top:26px}

/* section titles */
.section-title{font-family:"Audiowide",sans-serif;font-size:38px;color:var(--ink);width:1200px;left:0;text-align:center}
.section-title.light{color:var(--white)}

/* programs */
.program-card{top:722px;width:311px;height:422px;border:1px solid var(--line);border-radius:3px;background:var(--white);text-align:center}
.program-photo{height:202px;width:100%}
.program-card h3{font-size:19px;font-weight:700;color:var(--ink);margin-top:28px;text-transform:uppercase}
.program-card p{font-size:15.5px;line-height:28px;margin:16px 16px 0}
.read-more{display:inline-block;margin-top:16px;color:var(--green);font-size:15.5px;text-decoration:underline}

/* about */
.about{left:0;top:1207px;width:1200px;height:513px;background:linear-gradient(120deg,#1d7f1d,#2a8d2a 50%,#1a741a)}
.about-title{left:111px;top:88px;font-family:"Audiowide",sans-serif;font-size:38px;color:var(--white)}
.about-text{left:111px;top:152px;width:534px;color:var(--white);font-size:15.5px;line-height:30px;text-align:justify}
.about-text p+p{margin-top:13px}
.about .btn-outline{left:111px;top:402px;padding:13px 21px}
.about-photo{left:640px;top:40px;width:540px;height:440px;border-radius:40% 30% 20% 30%;background:radial-gradient(ellipse at 55% 45%,#d8d8d8 0%,#c43030 35%,#9a1f1f 55%,rgba(26,116,26,0) 72%)}

/* tournament */
.tournament-card{width:477px;height:118px;background:var(--white);box-shadow:0 0 8px rgba(0,0,0,.1);border-radius:3px}
.tournament-brand{left:20px;top:42px;width:130px;font-weight:800;font-size:15px;line-height:17px;color:var(--ink);text-transform:uppercase}
.tournament-info{left:180px;top:22px;font-size:16px;line-height:27px;color:var(--ink)}
.tournament-info .date{color:var(--green);display:block;margin-left:2px}

/* blog */
.blog{left:0;top:2343px;width:1200px;height:635px;background:radial-gradient(ellipse at 50% 0%,#2f9a2f,#1c7a1c 45%,#15641a)}
.blog-feature{left:115px;top:149px;width:417px;height:428px;border-radius:3px;overflow:hidden;background:linear-gradient(180deg,#c9d3dc 0%,#8f9aa6 45%,#3b3f45 80%,#1e1f22 100%)}
.blog-feature-text{left:27px;top:320px;width:360px;color:var(--white);font-size:18px;line-height:28px}
.blog-date{font-size:15.5px;display:flex;align-items:center;gap:7px;color:var(--white)}
.blog-feature-text .blog-date{margin-top:10px}
.blog-item{left:571px;width:518px;height:140px;border-bottom:1px solid rgba(255,255,255,.18)}
.blog-thumb{left:0;top:0;width:119px;height:118px;border-radius:3px;background:linear-gradient(180deg,#b7c0c9,#6b7580 60%,#d6dbe0)}
.blog-item-text{left:140px;top:-2px;width:378px;color:var(--white);font-size:17px;line-height:29px}
.blog-item-text .blog-date{margin-top:8px}

/* footer */
.site-footer{left:0;top:2978px;width:1200px;height:320px;background:var(--footer);color:var(--white)}
.footer-brand{left:111px;top:72px;font-weight:800;font-size:40px;line-height:42px;width:260px;text-transform:uppercase}
.footer-col{top:62px}
.footer-col h4{font-size:16px;font-weight:700;text-transform:uppercase;letter-spacing:.3px}
.footer-col ul{list-style:none;margin-top:20px;font-size:16px;line-height:30px}
.subscribe{left:851px;top:107px;width:238px;height:50px;background:var(--white);border-radius:2px;display:flex;align-items:center;justify-content:space-between;padding:0 18px 0 22px;color:#8a8a8a;font-size:15px}
.footer-rule{left:111px;top:252px;width:978px;height:1px;background:rgba(255,255,255,.3)}
.copyright{left:114px;top:278px;font-size:15.5px}
.footer-social{left:985px;top:278px;display:flex;gap:22px}
.footer-social span{width:18px;height:18px;border-radius:50%;background:var(--green-bright);display:block}
</style>
</head>
<body>

<header class="site-header abs">
  <div class="brand abs">Bramble Hockey Academy</div>
  <nav class="main-nav abs">
    <a class="active" href="#">Home</a><a href="#">About</a><a href="#">Programs</a><a href="#">Team</a><a href="#">Tournament</a>
  </nav>
  <div class="social abs" aria-label="Social links"><span></span><span></span><span></span><span></span></div>
</header>

<section class="hero abs">
  <div class="hero-photo abs" role="img" aria-label="Close-up of a hockey player's skates and stick on the ice"></div>
  <div class="hero-green abs"></div>
  <div class="hero-copy abs">
    <div class="hero-welcome">Welcome to</div>
    <h1 class="hero-title">BRAMBLE HOCKEY ACADEMY</h1>
    <a class="btn-outline" href="#">START NOW</a>
  </div>
</section>

<h2 class="section-title abs" style="top:645px">PROGRAMS</h2>

<article class="program-card abs" style="left:111px">
  <div class="program-photo" role="img" aria-label="Player skating in a winter rink" style="background:linear-gradient(180deg,#6f8aa5,#b5c6d6 60%,#dfe7ee)"></div>
  <h3>Winter Program</h3>
  <p>Excepteur sint occaecat cupidatat non proident, sunt in culpai offic deserunt mollit anim id est laborum.</p>
  <a class="read-more" href="#">READ MORE</a>
</article>
<article class="program-card abs" style="left:445px">
  <div class="program-photo" role="img" aria-label="Players racing for the puck" style="background:linear-gradient(180deg,#e7ebee,#c9cfd4 45%,#eef1f3)"></div>
  <h3>Spring Program</h3>
  <p>Excepteur sint occaecat cupidatat non proident, sunt in culpai offic deserunt mollit anim id est laborum.</p>
  <a class="read-more" href="#">READ MORE</a>
</article>
<article class="program-card abs" style="left:778px">
  <div class="program-photo" role="img" aria-label="Player in red stopping on the ice indoors" style="background:linear-gradient(180deg,#4a3a2e,#7b6a5a 55%,#cfd3d6)"></div>
  <h3>Summer Program</h3>
  <p>Excepteur sint occaecat cupidatat non proident, sunt in culpai offic deserunt mollit anim id est laborum.</p>
  <a class="read-more" href="#">READ MORE</a>
</article>

<section class="about abs">
  <h2 class="about-title abs">ABOUT US</h2>
  <div class="about-text abs">
    <p>Lorem ipsum dolor sit amet, consectetur adipiscing elit, sed do eiusmod tempor incididunt ut labore dolore magna aliqua. Quis ipsum suspendisse ultrices gravida. Risus commodo viverra maecenas accumsan.</p>
    <p>Sed ut perspiciatis unde omnis iste natus error sit voluptatem accusantium doloremque laudantium, totam rem aperiam, eaque ipsa quae ab illo inventore veritatis et quasi architecto beatae vitae dicta sunt explicabo. Nemo enim ipsam voluptatem quia voluptas.</p>
  </div>
  <a class="btn-outline abs" href="#">LEARN MORE</a>
  <div class="about-photo abs" role="img" aria-label="Two young players in red and white skating for the puck"></div>
</section>

<h2 class="section-title abs" style="top:1807px">TOURNAMENT</h2>

<div class="tournament-card abs" style="left:111px;top:1888px"><div class="tournament-brand abs">Bramble Hockey Academy</div><div class="tournament-info abs">2023 Women's World Championship<br>CANADA<span class="date">28 March 2023</span></div></div>
<div class="tournament-card abs" style="left:608px;top:1888px"><div class="tournament-brand abs">Bramble Hockey Academy</div><div class="tournament-info abs">2023 Women's World Championship<br>CANADA<span class="date">28 March 2023</span></div></div>
<div class="tournament-card abs" style="left:111px;top:2025px"><div class="tournament-brand abs">Bramble Hockey Academy</div><div class="tournament-info abs">2023 Women's World Championship<br>CANADA<span class="date">28 March 2023</span></div></div>
<div class="tournament-card abs" style="left:608px;top:2025px"><div class="tournament-brand abs">Bramble Hockey Academy</div><div class="tournament-info abs">2023 Women's World Championship<br>CANADA<span class="date">28 March 2023</span></div></div>
<div class="tournament-card abs" style="left:111px;top:2162px"><div class="tournament-brand abs">Bramble Hockey Academy</div><div class="tournament-info abs">2023 Women's World Championship<br>CANADA<span class="date">28 March 2023</span></div></div>
<div class="tournament-card abs" style="left:608px;top:2162px"><div class="tournament-brand abs">Bramble Hockey Academy</div><div class="tournament-info abs">2023 Women's World Championship<br>CANADA<span class="date">28 March 2023</span></div></div>

<section class="blog abs">
  <h2 class="section-title light abs" style="top:62px">LATEST BLOG</h2>
  <article class="blog-feature abs" role="img" aria-label="Two players facing off at centre ice">
    <div class="blog-feature-text abs">
      Lorem ipsum dolor sit amet, consectetur adipiscing.
      <div class="blog-date"><svg width="14" height="14" viewBox="0 0 14 14" fill="none" stroke="#fff" stroke-width="1.4"><rect x="1.5" y="2.5" width="11" height="10" rx="1"/><path d="M1.5 5.5h11M4.5 1v3M9.5 1v3"/></svg>28/03/23</div>
    </div>
  </article>

  <article class="blog-item abs" style="top:149px">
    <div class="blog-thumb abs" role="img" aria-label="Player in red skating toward the camera"></div>
    <div class="blog-item-text abs">Lorem ipsum dolor sit ametr adipiscing.ncididunt ut labore et dolore magna aliqua.
      <div class="blog-date"><svg width="14" height="14" viewBox="0 0 14 14" fill="none" stroke="#fff" stroke-width="1.4"><rect x="1.5" y="2.5" width="11" height="10" rx="1"/><path d="M1.5 5.5h11M4.5 1v3M9.5 1v3"/></svg>28/03/23</div>
    </div>
  </article>
  <article class="blog-item abs" style="top:304px">
    <div class="blog-thumb abs" role="img" aria-label="Players battling for the puck"></div>
    <div class="blog-item-text abs">Lorem ipsum dolor sit ametr adipiscing.ncididunt ut labore et dolore magna aliqua.
      <div class="blog-date"><svg width="14" height="14" viewBox="0 0 14 14" fill="none" stroke="#fff" stroke-width="1.4"><rect x="1.5" y="2.5" width="11" height="10" rx="1"/><path d="M1.5 5.5h11M4.5 1v3M9.5 1v3"/></svg>28/03/23</div>
    </div>
  </article>
  <article class="blog-item abs" style="top:460px">
    <div class="blog-thumb abs" role="img" aria-label="Player skating under arena lights" style="background:linear-gradient(180deg,#2e3339,#7d8792 60%,#d9dee3)"></div>
    <div class="blog-item-text abs">Lorem ipsum dolor sit ametr adipiscing.ncididunt ut labore et dolore magna aliqua.
      <div class="blog-date"><svg width="14" height="14" viewBox="0 0 14 14" fill="none" stroke="#fff" stroke-width="1.4"><rect x="1.5" y="2.5" width="11" height="10" rx="1"/><path d="M1.5 5.5h11M4.5 1v3M9.5 1v3"/></svg>28/03/23</div>
    </div>
  </article>
</section>

<footer class="site-footer abs">
  <div class="footer-brand abs">Bramble Hockey Academy</div>
  <div class="footer-col abs" style="left:434px">
    <h4>Home Navigation</h4>
    <ul><li>Home</li><li>About</li><li>Team</li><li>Tournament</li></ul>
  </div>
  <div class="footer-col abs" style="left:650px">
    <h4>Programs</h4>
    <ul><li>Spring Program</li><li>Summer Program</li><li>Winter Program</li></ul>
  </div>
  <div class="footer-col abs" style="left:847px"><h4>Subscribe</h4></div>
  <div class="subscribe abs">Email ID
    <svg width="20" height="18" viewBox="0 0 20 18"><path d="M1 1l18 8-18 8 4-8z" fill="#27a52a"/></svg>
  </div>
  <div class="footer-rule abs"></div>
  <div class="copyright abs">2023 Bramble Hockey Academy. All rights reserved.</div>
  <div class="footer-social abs" aria-label="Social links"><span></span><span></span><span></span></div>
</footer>

</body>
</html>
```